Bookcover: Ways to Turn Into a Bold Pathfinder

I am publishing a super-low-cost innovation book for €4,99 on Quillmere Open Press to help everyone become a great innovator: young ambitious people without college education nor a big budget. Do you want to help me?

Brief:
Design a book cover 1600 x 2560 pixels for QOP.
Main title: Ways to Turn Into a Bold Pathfinder
Sub title: mindset - insights - skills & tools
Author: Joost ter Brakel
Design: captive, and appealing to everyone
Target Group: young ambitious people without college education

For quillmere please format the height/width ratio of 1.6:1

```html
<!DOCTYPE html>
<html lang="en">
<head>
<meta charset="utf-8">
<title>Ways to Turn Into a Bold Pathfinder — Book Cover</title>
<link rel="stylesheet" href="https://fonts.googleapis.com/css2?family=Bebas+Neue&family=Montserrat:wght@700&display=swap">
<style>
  :root {
    --stage-grey: #a09fa0;
    --paper: #ffffff;
    --ink: #000000;
    --signal-red: #d10000;
    --art-light: #ececec;
    --art-mid: #cfcfcf;
  }
  html, body {
    margin: 0;
    width: 1200px;
    height: 1200px;
    overflow: hidden;
    background: var(--stage-grey);
  }
  .cover {
    position: absolute;
    left: 293px;
    top: 140px;
    width: 614px;
    height: 920px;
    background: var(--paper);
    overflow: hidden;
  }
  .cover p,
  .cover h1 {
    margin: 0;
  }
  .title {
    font-family: "Bebas Neue", "Oswald", sans-serif;
    font-weight: 400;
  }
  .title span {
    position: absolute;
    left: 0;
    right: 0;
    text-align: center;
    line-height: 1;
    white-space: nowrap;
  }
  .title-lead {
    top: 37px;
    font-size: 84px;
    color: var(--ink);
  }
  .title-accent {
    top: 99px;
    font-size: 292px;
    color: var(--signal-red);
  }
  .title-main {
    top: 329px;
    font-size: 150px;
    color: var(--ink);
  }
  .cover-art {
    position: absolute;
    left: 179px;
    top: 475px;
    width: 245px;
    height: 344px;
    background: radial-gradient(ellipse at 55% 30%, var(--art-mid) 0%, var(--art-light) 55%, var(--paper) 100%);
  }
  .subtitle-band {
    position: absolute;
    left: 0;
    top: 833px;
    width: 100%;
    height: 41px;
    background: var(--signal-red);
    color: var(--paper);
    font-family: "Montserrat", sans-serif;
    font-weight: 700;
    font-size: 25px;
    letter-spacing: 1px;
    line-height: 41px;
    text-align: center;
    text-transform: uppercase;
    white-space: nowrap;
  }
  .author {
    position: absolute;
    left: 0;
    top: 884px;
    width: 100%;
    line-height: 30px;
    text-align: center;
    font-family: "Montserrat", sans-serif;
    font-weight: 700;
    font-size: 21px;
    letter-spacing: 1px;
    color: var(--ink);
    text-transform: uppercase;
    white-space: nowrap;
  }
</style>
</head>
<body>
  <main class="cover">
    <h1 class="title">
      <span class="title-lead">Ways to Turn Into a</span>
      <span class="title-accent">Bold</span>
      <span class="title-main">Pathfinder</span>
    </h1>
    <div class="cover-art" role="img" aria-label="Line drawing of a head in profile with a grey brain and a colourful light bulb inside"></div>
    <p class="subtitle-band">Mindset - Insights - Skills &amp; Tools</p>
    <p class="author">Joost ter Brakel</p>
  </main>
</body>
</html>
```